Carrow Facilities Services Business Card.

We need a card for Carrow Facilities Services with a new look. We also have service and supply partners that we would like to have on the card. Coatrivex is a surface application company, Carrow Facilities is a facilities services business, Bellmont Supply Co is a Facilities supply business, Prevla is a product that we use that powers our business.

```html
<!DOCTYPE html>
<html lang="en">
<head>
<meta charset="utf-8">
<title>Carrow Facilities Services Business Card</title>
<link rel="stylesheet" href="https://fonts.googleapis.com/css2?family=Open+Sans:wght@700&family=Roboto:wght@400;700&display=swap">
<style>
  :root {
    --brand-blue: #0e76bc;
    --brand-green: #39b54a;
    --paper: #ffffff;
    --ink-grey: #555555;
    --rule-grey: #8a8a8a;
    --backdrop: #a3a3a3;
  }
  * { margin: 0; padding: 0; box-sizing: border-box; }
  html, body { width: 1200px; height: 1200px; overflow: hidden; }
  body { background: var(--backdrop); position: relative; font-family: "Roboto", Arial, sans-serif; }

  .card { position: absolute; top: 303px; height: 594px; overflow: hidden; }

  .card-front { left: 200px; width: 369px; background: var(--brand-green); }
  .card-front .sky { position: absolute; left: 0; top: 0; width: 100%; height: 56%; background: var(--brand-blue); }
  .card-front .disc {
    position: absolute; left: 50%; top: 50%; width: 200px; height: 200px;
    margin: -100px 0 0 -100px; border-radius: 50%; background: var(--paper);
  }

  .card-back { left: 599px; width: 364px; background: var(--paper); text-align: center; }

  .brand { position: absolute; left: 26px; top: 108px; display: flex; align-items: center; gap: 12px; }
  .brand-dot { width: 64px; height: 64px; border-radius: 50%; background: var(--brand-blue); flex: none; }
  .brand-name { text-align: left; color: var(--brand-blue); font-family: "Roboto", Arial, sans-serif; font-weight: 700; line-height: 1; }
  .brand-name .primary { display: block; font-size: 58px; letter-spacing: -0.5px; }
  .brand-name .secondary { display: block; font-size: 21px; margin-top: 4px; }

  .person { position: absolute; left: 0; right: 0; top: 333px; }
  .person-name { font-family: "Open Sans", Arial, sans-serif; font-weight: 700; font-size: 27px; color: var(--brand-blue); line-height: 1.1; }
  .person-title { font-size: 17px; color: var(--ink-grey); line-height: 1.2; }

  .icon-row { position: absolute; left: 87px; width: 190px; top: 396px; display: flex; align-items: center; gap: 4px; }
  .icon-row .rule { flex: 1; height: 1px; background: var(--rule-grey); }
  .icon-row .icons { display: flex; gap: 4px; }
  .icon { width: 25px; height: 25px; border-radius: 3px; background: var(--brand-blue); display: block; }

  .contact { position: absolute; left: 0; right: 0; top: 431px; font-size: 17px; color: var(--ink-grey); line-height: 22px; }
  .divider { position: absolute; left: 88px; width: 195px; top: 507px; height: 1px; background: var(--rule-grey); }
  .address { position: absolute; left: 0; right: 0; top: 518px; font-size: 17px; color: var(--ink-grey); line-height: 22px; }
</style>
</head>
<body>

<div class="card card-front" role="img" aria-label="Card front: blue and green brand fields">
  <div class="sky"></div>
  <div class="disc"></div>
</div>

<div class="card card-back">
  <div class="brand">
    <span class="brand-dot"></span>
    <div class="brand-name">
      <span class="primary">Carrow</span>
      <span class="secondary">Facilities Services</span>
    </div>
  </div>

  <div class="person">
    <div class="person-name">Daniel Reeve</div>
    <div class="person-title">Managing Director</div>
  </div>

  <div class="icon-row">
    <span class="rule"></span>
    <span class="icons">
      <svg class="icon" viewBox="0 0 25 25" aria-label="Phone">
        <rect width="25" height="25" rx="3" fill="#0e76bc"/>
        <path d="M5 10 Q12.5 5 20 10 L18 12 L16 10.5 L16 9 Q12.5 8 9 9 L9 10.5 L7 12 Z" fill="#fff"/>
        <rect x="7.5" y="12" width="10" height="6" rx="1" fill="#fff"/>
      </svg>
      <svg class="icon" viewBox="0 0 25 25" aria-label="Email">
        <rect width="25" height="25" rx="3" fill="#0e76bc"/>
        <rect x="5" y="7.5" width="15" height="10" fill="none" stroke="#fff" stroke-width="1.4"/>
        <path d="M5 7.5 L12.5 13 L20 7.5" fill="none" stroke="#fff" stroke-width="1.4"/>
      </svg>
      <svg class="icon" viewBox="0 0 25 25" aria-label="Website">
        <rect width="25" height="25" rx="3" fill="#0e76bc"/>
        <circle cx="12.5" cy="12.5" r="7.5" fill="#fff"/>
        <circle cx="10.5" cy="11" r="2.8" fill="#0e76bc"/>
        <circle cx="15" cy="15.5" r="1.8" fill="#0e76bc"/>
      </svg>
    </span>
    <span class="rule"></span>
  </div>

  <div class="contact">
    <div>044-555 010 274</div>
    <div>info@webname.com</div>
    <div>www.websitename.com</div>
  </div>

  <div class="divider"></div>

  <div class="address">
    <div>421, Address line here,</div>
    <div>45452,Country Name</div>
  </div>
</div>

</body>
</html>
```